Flyer für Immobilienmakler
Zielgruppe
Wir, die Kessler Immobilien GmbH, vermitteln Häuser, Wohnungen und Grundstücke, unsere Zielgruppe sind Verkäufer und Kaufinteressenten aus der Region, Immobilien zur Vermittlung gesucht
Aufgabenstellung
Unverbindliche Ersteinschätzung, Ansprechpartner vor Ort, regionale Marktkenntnis. Max. Din A 5, Immobilien zur Vermittlung gesucht.
- Flyer nur zur Immobilienvermittlung

```html
<!DOCTYPE html>
<html lang="de">
<head>
<meta charset="utf-8">
<title>Kessler Immobilien – Flyer Immobilienvermittlung</title>
<link href="https://fonts.googleapis.com/css2?family=DM+Serif+Display&family=Roboto:wght@400;500&family=Nunito+Sans:wght@400;700&display=swap" rel="stylesheet">
<style>
  :root{
    --stage:#5a5664;
    --purple:#6f58a6;
    --purple-soft:rgba(111,88,166,0.92);
    --green:#13a37f;
    --mint:#cddbd6;
    --ink:#2a2a33;
    --text:#57575f;
    --white:#ffffff;
    --serif:'DM Serif Display', Georgia, serif;
    --sans:'Roboto', Arial, sans-serif;
    --contact:'Nunito Sans', Arial, sans-serif;
  }
  *{box-sizing:border-box;margin:0;padding:0}
  html,body{width:1200px;height:1200px;overflow:hidden;background:var(--stage)}
  .flyer{position:absolute;left:190px;top:20px;width:820px;height:1160px;background:var(--white);overflow:hidden;box-shadow:0 14px 40px rgba(0,0,0,.35)}
  .hero{position:absolute;left:0;top:0;width:820px;height:520px}
  .hero-title{position:absolute;left:48px;top:40px;font-family:var(--serif);font-size:50px;line-height:47px;color:var(--white);letter-spacing:-1.6px;font-weight:400}
  .brand{position:absolute;left:548px;top:78px;display:flex;align-items:center;gap:8px;font-family:var(--serif);font-size:17px;color:var(--ink)}
  .brand-square{width:12px;height:12px;background:var(--ink)}
  .intro{position:absolute;left:48px;top:372px;width:600px}
  .section-title{font-family:var(--serif);font-weight:400;color:var(--ink);letter-spacing:-.4px}
  .intro h2{font-size:28px;line-height:34px}
  .copy{font-family:var(--sans);font-size:17px;line-height:22px;color:var(--text)}
  .intro .copy{margin-top:16px;width:600px}
  .copy + .copy{margin-top:10px}
  .rule{position:absolute;left:48px;width:728px;height:7px;background:var(--purple)}
  .columns{position:absolute;left:48px;top:624px;width:760px;display:flex}
  .col-left{width:393px}
  .col-right{width:360px}
  .columns h3{font-size:23px;line-height:28px;margin-bottom:12px}
  .col-left h4{font-family:var(--sans);font-weight:500;font-size:17px;color:var(--ink);margin-bottom:6px}
  .col-left .copy{width:360px}
  .benefits{list-style:none;margin-left:10px}
  .benefits li{position:relative;padding-left:23px;margin-bottom:10px;width:330px}
  .benefits svg{position:absolute;left:0;top:4px}
  .wanted{position:absolute;left:0;top:884px;width:820px;height:186px;background:var(--mint);text-align:center}
  .wanted h2{font-size:28px;line-height:32px;margin-top:22px}
  .wanted .copy{margin-top:4px}
  .wanted-list{position:absolute;left:47px;top:93px;width:727px;display:flex;gap:11px}
  .wanted-item{flex:1;height:64px;background:var(--white);border-radius:3px;display:flex;align-items:center;padding-left:11px;gap:18px;font-family:var(--sans);font-weight:500;font-size:21px;color:var(--ink)}
  .contact{position:absolute;left:0;top:1070px;width:820px;height:90px;background:var(--green);color:var(--white);font-family:var(--contact);font-size:16px;line-height:22px}
  .contact-label{position:absolute;left:47px;top:20px;font-family:var(--serif);font-size:24px}
  .contact-company{position:absolute;left:214px;top:20px}
  .contact-lines{position:absolute;left:507px;top:20px}
  .contact strong{font-weight:700}
</style>
</head>
<body>
<main class="flyer">
  <svg class="hero" viewBox="0 0 820 520" aria-hidden="false">
    <defs>
      <linearGradient id="photo" x1="0" y1="0" x2="0.3" y2="1">
        <stop offset="0" stop-color="#b9c2d6"/>
        <stop offset="0.35" stop-color="#9b8a86"/>
        <stop offset="0.6" stop-color="#7f9a62"/>
        <stop offset="1" stop-color="#6ec9c4"/>
      </linearGradient>
      <linearGradient id="tint" x1="0" y1="0" x2="1" y2="0.3">
        <stop offset="0" stop-color="#6f58a6" stop-opacity="0.95"/>
        <stop offset="0.55" stop-color="#6f58a6" stop-opacity="0.55"/>
        <stop offset="1" stop-color="#6f58a6" stop-opacity="0"/>
      </linearGradient>
    </defs>
    <polygon points="0,0 820,0 820,494 0,224" fill="url(#photo)" role="img" aria-label="Foto eines Landhauses mit Pool und Garten in ländlicher Umgebung"/>
    <polygon points="0,0 820,0 820,494 0,224" fill="url(#tint)"/>
    <polygon points="0,224 820,492 820,508 0,232" fill="var(--green)"/>
    <polygon points="0,332 229,252 820,447 820,490 229,289 0,366" fill="var(--purple)"/>
  </svg>

  <h1 class="hero-title">Ihr Regionaler<br>Partner für<br>Immobilienvermittlung</h1>

  <div class="brand"><span class="brand-square"></span>Kessler Immobilien GmbH</div>

  <section class="intro">
    <h2 class="section-title">Kompetente<br>Immobilienlösungen Vor Ort</h2>
    <p class="copy">Die Kessler Immobilien GmbH mit Sitz in Lindental ist Ihr zuverlässiger Ansprechpartner rund um die Vermittlung von Immobilien.</p>
    <p class="copy">Mit fundierter regionaler Marktkenntnis und persönlicher Betreuung unterstützen wir Eigentümer, Käufer, Verkäufer sowie Mietinteressenten.</p>
  </section>

  <div class="rule" style="top:585px"></div>

  <section class="columns">
    <div class="col-left">
      <h3 class="section-title">Unsere Leistung</h3>
      <h4>Immobilienvermittlung</h4>
      <p class="copy">Ob Verkauf oder Vermietung – wir kümmern uns zuverlässig um die Vermittlung von Häusern, Wohnungen, Grundstücken und Gebäuden.</p>
      <p class="copy">Dabei begleiten wir Sie persönlich von der ersten Beratung bis zum erfolgreichen Abschluss.</p>
    </div>
    <div class="col-right">
      <h3 class="section-title">Warum Kessler Immobilien?</h3>
      <ul class="benefits copy">
        <li><svg width="12" height="12" viewBox="0 0 12 12"><path d="M2 2l4 4-4 4M6 2l4 4-4 4" fill="none" stroke="var(--purple)" stroke-width="1.8"/></svg>Persönlicher Ansprechpartner vor Ort</li>
        <li><svg width="12" height="12" viewBox="0 0 12 12"><path d="M2 2l4 4-4 4M6 2l4 4-4 4" fill="none" stroke="var(--purple)" stroke-width="1.8"/></svg>Umfassende regionale Marktkenntnis</li>
        <li><svg width="12" height="12" viewBox="0 0 12 12"><path d="M2 2l4 4-4 4M6 2l4 4-4 4" fill="none" stroke="var(--purple)" stroke-width="1.8"/></svg>Transparente und professionelle Abwicklung</li>
        <li><svg width="12" height="12" viewBox="0 0 12 12"><path d="M2 2l4 4-4 4M6 2l4 4-4 4" fill="none" stroke="var(--purple)" stroke-width="1.8"/></svg>Zuverlässiger Partner für Eigentümer und Investoren</li>
      </ul>
    </div>
  </section>

  <div class="rule" style="top:880px"></div>

  <section class="wanted">
    <h2 class="section-title">Immobilien Zur Vermittlung Gesucht</h2>
    <p class="copy">Wir sind laufend auf der Suche nach:</p>
    <div class="wanted-list">
      <div class="wanted-item">
        <svg width="38" height="40" viewBox="0 0 38 40" fill="none" stroke="var(--ink)" stroke-width="1.6"><path d="M2 20L19 4l17 16M7 16v22h24V16M12 38V26h7v12M22 25h7v7h-7zM25.5 25v7M22 28.5h7M27 7h4v6"/></svg>
        Häusern
      </div>
      <div class="wanted-item">
        <svg width="40" height="40" viewBox="0 0 40 40" fill="none" stroke="var(--ink)" stroke-width="1.6"><path d="M4 38V6h10V2h12v4h10v32zM2 38h36M9 11h5v4H9zM17 11h6v4h-6zM26 11h5v4h-5zM9 19h5v4H9zM17 19h6v4h-6zM26 19h5v4h-5zM9 27h5v4H9zM26 27h5v4h-5zM17 28h6v10h-6z"/></svg>
        Wohnungen
      </div>
      <div class="wanted-item">
        <svg width="42" height="36" viewBox="0 0 42 36" fill="none" stroke="var(--ink)" stroke-width="1.6"><path d="M6 14c2-6 8-8 12-5 3-4 10-4 13 0 4-1 7 2 6 5M2 16h38M2 22h38M4 16l-2 18h38l-2-18M14 22l-3 12M28 22l3 12M21 22v12M2 28h38"/></svg>
        Grundstücken
      </div>
    </div>
  </section>

  <footer class="contact">
    <div class="contact-label">Kontakt</div>
    <div class="contact-company"><strong>Kessler Immobilien GmbH</strong><br>94121 Lindental, Mühlweg 7</div>
    <div class="contact-lines"><strong>T</strong>: +49 85 00 412380-0<br><strong>E</strong>: kontakt@kessler-lindental.de</div>
  </footer>
</main>
</body>
</html>
```